Stylish new business card needed!

Hello everyone! I am in need of a new business card design for an alarm company here in Hurricane WV. I have all fonts, color codes and logos provided for you use! We are a young company and like the style of a clean sleek looking business card. Would like it double sided, one side holding the logo and the other with your design!
Target Market(s)
The people that are looking for the newest tech for home automation and security
Industry/Entity Type
Alarm services; Home automation
Contact Information for Business Card
Name of person; position (Sales; Installer); Phone Number (555.418.7260); Employee cell Number; Website (www.GuardedByVelk.example); Employee Email; Double sided
Look and feel
Each slider illustrates characteristics of the customer's brand and the style your logo design should communicate.

```html
<!DOCTYPE html>
<html lang="en">
<head>
<meta charset="utf-8">
<title>Guarded By Velk – Business Card</title>
<link rel="stylesheet" href="https://fonts.googleapis.com/css2?family=Arimo:wght@400;700&display=swap">
<style>
  :root {
    --backdrop: #2b2b2e;
    --card: #232226;
    --card-edge: #1b1a1d;
    --orange: #f08a3c;
    --grey: #a6a6a6;
    --white: #f2f2f2;
    --emboss: #1a191c;
    --emboss-light: #2e2d31;
    --rule: #8a8a8a;
  }
  * { box-sizing: border-box; margin: 0; padding: 0; }
  html, body {
    width: 1200px; height: 780px; overflow: hidden;
    background: var(--backdrop);
    font-family: "Arimo", Arial, sans-serif;
  }
  .stage {
    position: relative; width: 1200px; height: 780px;
    display: flex; align-items: center; justify-content: center; gap: 40px;
  }
  .card {
    position: relative; width: 540px; height: 310px;
    background: var(--card);
    border-radius: 18px;
    box-shadow: 0 3px 0 var(--card-edge), 0 14px 30px rgba(0,0,0,.45);
    overflow: hidden;
  }

  /* Front */
  .brand { position: absolute; left: 34px; top: 92px; width: 230px; }
  .brand-name {
    display: flex; align-items: center; gap: 10px;
    font-size: 27px; font-weight: 700; color: var(--grey);
    letter-spacing: .5px; line-height: 1;
  }
  .brand-dot { width: 16px; height: 16px; border-radius: 50%; background: var(--orange); flex: none; }
  .tagline {
    margin-top: 14px; margin-left: 26px;
    font-size: 8.5px; font-weight: 700; color: var(--orange);
    text-transform: uppercase; letter-spacing: .6px;
  }
  .divider { position: absolute; left: 0; top: 0; }
  .details { position: absolute; left: 300px; top: 88px; }
  .person-name { font-size: 25px; font-weight: 700; line-height: 1; }
  .person-name .first { color: var(--orange); }
  .person-name .last { color: var(--grey); }
  .person-role { margin-top: 6px; font-size: 13px; font-weight: 700; color: var(--white); }
  .contacts { list-style: none; margin-top: 16px; }
  .contacts li {
    display: flex; align-items: center; gap: 8px;
    font-size: 13px; color: var(--white); line-height: 20px;
  }
  .contacts svg { width: 12px; height: 12px; flex: none; }

  /* Back */
  .back .brand-mark {
    position: absolute; inset: 0;
    display: flex; flex-direction: column; align-items: center; justify-content: center;
  }
  .back .brand-name {
    font-size: 50px; color: var(--emboss);
    text-shadow: 0 1px 0 var(--emboss-light);
  }
  .back .tagline {
    margin: 16px 0 0; font-size: 11px; color: var(--emboss);
    text-shadow: 0 1px 0 var(--emboss-light);
  }
</style>
</head>
<body>
<main class="stage">
  <section class="card front" aria-label="Card front">
    <div class="brand">
      <div class="brand-name"><span class="brand-dot"></span>Guarded By Velk</div>
      <p class="tagline">Automation and Security Services</p>
    </div>

    <svg class="divider" width="540" height="310" aria-hidden="true">
      <line x1="300" y1="38" x2="252" y2="272" stroke="var(--rule)" stroke-width="1"/>
    </svg>

    <div class="details">
      <h1 class="person-name"><span class="first">Mara</span> <span class="last">Delin</span></h1>
      <p class="person-role">Sales; Installer</p>
      <ul class="contacts">
        <li>
          <svg viewBox="0 0 12 12" aria-hidden="true"><path d="M2.5 1 L4.5 1 L5.3 3.4 L4 4.3 C4.6 5.8 6.2 7.4 7.7 8 L8.6 6.7 L11 7.5 L11 9.5 C11 10.3 10.3 11 9.5 11 C5 11 1 7 1 2.5 C1 1.7 1.7 1 2.5 1 Z" fill="var(--orange)"/></svg>
          555.418.7260
        </li>
        <li>
          <svg viewBox="0 0 12 12" aria-hidden="true"><rect x="3" y="0.8" width="6" height="10.4" rx="1.2" fill="none" stroke="var(--orange)" stroke-width="1.2"/><circle cx="6" cy="9.4" r=".7" fill="var(--orange)"/></svg>
          555.907.3314
        </li>
        <li>
          <svg viewBox="0 0 12 12" aria-hidden="true"><circle cx="6" cy="6" r="5" fill="none" stroke="var(--orange)" stroke-width="1.1"/><ellipse cx="6" cy="6" rx="2.2" ry="5" fill="none" stroke="var(--orange)" stroke-width="1"/><line x1="1" y1="6" x2="11" y2="6" stroke="var(--orange)" stroke-width="1"/></svg>
          www.GuardedByVelk.example
        </li>
        <li>
          <svg viewBox="0 0 12 12" aria-hidden="true"><rect x="0.8" y="2.3" width="10.4" height="7.4" rx="1" fill="none" stroke="var(--orange)" stroke-width="1.1"/><path d="M1 2.8 L6 6.6 L11 2.8" fill="none" stroke="var(--orange)" stroke-width="1.1"/></svg>
          info@GuardedByVelk.example
        </li>
      </ul>
    </div>
  </section>

  <section class="card back" aria-label="Card back">
    <div class="brand-mark">
      <div class="brand-name">Guarded By Velk</div>
      <p class="tagline">Automation and Security Services</p>
    </div>
  </section>
</main>
</body>
</html>
```